Business Card Design Project

colors are orange and blue (larkmoor valley university football orange and blue.

need jpeg to build a business card
fill 2/3 of biz card on top half of card

I need a orange swoosh (looks like a line painted by a paintbrush used on outside of the house) the orange line should trail off at the end.
underscore the orange swoosh with a blue shelf.make the left side of the shelf ornamental like it fits into the corner of the wall

Target Market(s)

life coach business consultant. orange means enthusiasm and blue is stability and competence

Industry/Entity Type

University

Requirements
Must have
• add very simple paint example. orange must be larkmoor valley u football color orange and same w/ the blue. orange is to be like a wide paint brush. blue below will look like a shelf w/ an edge that fits into a corner wall.

```html
<!DOCTYPE html>
<html lang="en">
<head>
<meta charset="utf-8">
<title>Larkmoor Valley University – Business Card</title>
<link rel="stylesheet" href="https://fonts.googleapis.com/css2?family=Oswald:wght@700&display=swap">
<style>
  :root {
    --card-white: #ffffff;
    --card-border: #9a9a9a;
    --brand-orange: #f5501e;
    --brand-orange-soft: #ffb397;
    --brand-blue: #0a3cf0;
  }
  html, body {
    margin: 0;
    padding: 0;
    width: 1200px;
    height: 696px;
    overflow: hidden;
    background: var(--card-white);
  }
  .business-card {
    position: relative;
    width: 1200px;
    height: 696px;
    box-sizing: border-box;
    border: 2px solid var(--card-border);
    background: var(--card-white);
    overflow: hidden;
  }
  .paint-art {
    position: absolute;
    inset: 0;
    width: 100%;
    height: 100%;
  }
  .brand-mark {
    position: absolute;
    left: 56px;
    top: 40px;
    display: flex;
    align-items: center;
    gap: 16px;
  }
  .brand-dot {
    width: 44px;
    height: 44px;
    border-radius: 50%;
    background: var(--brand-orange);
    flex: none;
  }
  .brand-name {
    margin: 0;
    font-family: "Oswald", sans-serif;
    font-weight: 700;
    font-size: 40px;
    line-height: 1.05;
    text-transform: uppercase;
    color: var(--brand-blue);
  }
</style>
</head>
<body>
  <div class="business-card">
    <svg class="paint-art" viewBox="0 0 1200 696" aria-hidden="true">
      <defs>
        <radialGradient id="corner-glow" cx="1200" cy="0" r="760" gradientUnits="userSpaceOnUse">
          <stop offset="0" stop-color="var(--brand-orange-soft)" stop-opacity="0.75"/>
          <stop offset="1" stop-color="var(--brand-orange-soft)" stop-opacity="0"/>
        </radialGradient>
        <linearGradient id="brush-fill" x1="40" y1="0" x2="1200" y2="0" gradientUnits="userSpaceOnUse">
          <stop offset="0" stop-color="var(--brand-orange)" stop-opacity="0"/>
          <stop offset="0.3" stop-color="var(--brand-orange)" stop-opacity="0.55"/>
          <stop offset="1" stop-color="var(--brand-orange)" stop-opacity="1"/>
        </linearGradient>
        <linearGradient id="shelf-fill" x1="230" y1="0" x2="1200" y2="0" gradientUnits="userSpaceOnUse">
          <stop offset="0" stop-color="var(--brand-blue)" stop-opacity="0.85"/>
          <stop offset="1" stop-color="var(--brand-blue)" stop-opacity="1"/>
        </linearGradient>
      </defs>

      <rect class="paint-glow" x="0" y="0" width="1200" height="360" fill="url(#corner-glow)"/>

      <path class="paint-brush" fill="url(#brush-fill)"
            d="M40,318 C300,230 650,175 1200,150 V212 C700,222 320,262 40,318 Z"/>
      <path class="paint-bristle" fill="none" stroke="var(--card-white)" stroke-width="2" stroke-opacity="0.5"
            d="M320,262 C600,205 900,180 1200,170"/>
      <path class="paint-bristle" fill="none" stroke="var(--card-white)" stroke-width="1.5" stroke-opacity="0.4"
            d="M480,240 C720,210 960,196 1200,193"/>

      <path class="shelf-board" fill="url(#shelf-fill)"
            d="M230,292 C520,258 820,240 1200,236 V254 C820,258 520,276 230,310 Z"/>
      <path class="shelf-bracket" fill="var(--brand-blue)"
            d="M230,292 L230,352 Q238,318 268,306 Z"/>
      <circle class="shelf-bracket-knob" cx="230" cy="358" r="6" fill="var(--brand-blue)"/>
    </svg>

    <div class="brand-mark">
      <div class="brand-dot"></div>
      <p class="brand-name">Larkmoor<br>Valley</p>
    </div>
  </div>
</body>
</html>
```